business card - Helicopter Flight Services, Flight School, etc.

We need a business card design for a new helicopter service.

We offer Helicopter Flight Services, Aerial Filming & Photography, Flight School, and Helicopter Tours. In that order.

Summit BladeAir, Inc.
Dennis Tollerby
SummitBladeair@Kestmail.com
626-418-7352

Based at the Brenwick Airport in Van Nuys, CA. The final design should communicate integrity and safety. Pictures or logos at your discretion.

Card back side - surprise me.

```html
<!DOCTYPE html>
<html lang="en">
<head>
<meta charset="utf-8">
<title>Summit BladeAir, Inc. – Business Card</title>
<link href="https://fonts.googleapis.com/css2?family=Open+Sans:wght@400;600&display=swap" rel="stylesheet">
<style>
  :root {
    --backdrop: #e9e8ee;
    --lavender: #9ea7d3;
    --lavender-light: #c3c9e8;
    --lavender-deep: #6f7cb8;
    --paper: #ffffff;
    --ink: #1c1c1c;
    --rule: #3a3a3a;
  }
  * { margin: 0; padding: 0; box-sizing: border-box; }
  html, body { width: 1200px; height: 902px; overflow: hidden; background: var(--backdrop); }
  .sheet {
    width: 1200px; height: 902px;
    display: flex; flex-direction: column; align-items: center; justify-content: space-evenly;
  }
  .card {
    width: 700px; height: 400px; position: relative;
    box-shadow: 0 4px 14px rgba(0,0,0,.15);
  }

  /* Back side */
  .card-back {
    background: var(--lavender);
    display: flex; flex-direction: column; align-items: center; justify-content: center;
    font-family: "Open Sans", sans-serif;
  }
  .back-name {
    font-weight: 600; font-size: 46px;
    color: var(--lavender-light);
  }
  .back-services {
    margin-top: 8px;
    font-weight: 400; font-size: 22px;
    color: var(--lavender-light);
  }

  /* Front side */
  .card-front { background: var(--lavender); padding: 16px; }
  .front-panel {
    width: 100%; height: 100%; background: var(--paper);
    border: 2px solid var(--lavender-light);
    position: relative;
    font-family: "Open Sans", sans-serif;
  }
  .front-name {
    position: absolute; left: 100px; right: 24px; top: 66px;
    text-align: center;
    font-weight: 600; font-size: 40px; line-height: 1.2;
    color: var(--lavender-deep);
  }
  .front-rule {
    position: absolute; left: 100px; right: 24px; top: 134px;
    height: 2px; background: var(--rule);
  }
  .contact {
    position: absolute; left: 100px; right: 24px; top: 158px;
    text-align: center; color: var(--ink);
    font-size: 17px; line-height: 1.45;
  }
  .contact-person { font-size: 25px; color: var(--lavender-deep); margin-bottom: 10px; }
</style>
</head>
<body>
<main class="sheet">
  <section class="card card-back" aria-label="Card back">
    <p class="back-name">Summit BladeAir, Inc.</p>
    <p class="back-services">Airport · Tour guide · Heliport</p>
  </section>

  <section class="card card-front" aria-label="Card front">
    <div class="front-panel">
      <h1 class="front-name">Summit BladeAir, Inc.</h1>
      <div class="front-rule"></div>
      <div class="contact">
        <p class="contact-person">Dennis Tollerby</p>
        <p>626-418-7352</p>
        <p>SummitBladeair@Kestmail.com</p>
        <p>2840 W. Larkfield Ave. Ste.B</p>
        <p>Corvale, CA 91688</p>
      </div>
    </div>
  </section>
</main>
</body>
</html>
```